Visitenkarten-Design für Sonnen-/Fensterschutz
Zielgruppe
KLW GmbH ist eine Firma, die Sonnenschutz und Fensterschutz anbieten.
'Ihr kompetenter Partner in Sachen Sonnenschutz- , Fenster- und Türtechnik. Sie erhalten echtes Handwerk aus dem Mühlviertel zu fairen Preisen.'
Unsere Zielgruppe sind Personen mit Haus, die am Land leben.
Firmenname: KLW GmbH
Slogan: Fenster & Sonnenschutz
Aufgabenstellung
Hier befindet sich das Logodesign: https://dx.qv/t-QwLpo7RbNs
Bitte ein schlichtes Design bereitstellen mit einer Dummy-Person:
Jonas Weidlinger + Telefonnummer + Email
Die finalen Daten bitte erst am Schluss berücksichtigen (für Gewinnerdesign)
Gerne auch hintern + vorne bedruckbar bereitstellen.

```html
<!DOCTYPE html>
<html lang="de">
<head>
<meta charset="utf-8">
<title>KLW GmbH – Visitenkarte</title>
<link rel="stylesheet" href="https://fonts.googleapis.com/css2?family=Arimo:wght@400;700&display=swap">
<style>
  :root {
    --bg: #d9d9d9;
    --orange: #e2703a;
    --red: #d83a36;
    --white: #ffffff;
    --ink: #3a3a3a;
    --ink-soft: #555555;
  }
  * { margin: 0; padding: 0; box-sizing: border-box; }
  html, body { width: 1200px; height: 842px; overflow: hidden; }
  body {
    background: var(--bg);
    font-family: "Arimo", Arial, sans-serif;
    position: relative;
  }
  .card {
    position: absolute;
    top: 258px;
    width: 520px;
    height: 326px;
    overflow: hidden;
    box-shadow: 0 6px 18px rgba(0,0,0,.18);
  }
  .card--front {
    left: 50px;
    background: linear-gradient(90deg, var(--orange) 0%, var(--red) 70%);
  }
  .card--back { left: 630px; background: var(--white); }

  .front-brand {
    position: absolute;
    inset: 0;
    display: flex;
    align-items: center;
    justify-content: center;
    gap: 14px;
    color: var(--white);
  }
  .front-brand__square { width: 26px; height: 26px; background: var(--white); }
  .front-brand__name { font-weight: 700; font-size: 52px; letter-spacing: 2px; }

  .back-shape { position: absolute; inset: 0; }

  .back-brand {
    position: absolute;
    top: 88px;
    right: 52px;
    display: flex;
    align-items: center;
    gap: 10px;
    color: var(--red);
  }
  .back-brand__square { width: 16px; height: 16px; background: var(--red); }
  .back-brand__name { font-weight: 700; font-size: 32px; letter-spacing: 1px; }

  .contact {
    position: absolute;
    left: 46px;
    top: 52px;
    color: var(--ink);
    font-size: 13px;
    line-height: 1.3;
  }
  .contact__name { font-weight: 700; font-size: 20px; line-height: 1.2; }
  .contact__role { color: var(--ink-soft); margin-bottom: 9px; }
  .contact__heading { font-weight: 700; font-size: 13px; }
  .contact__list { display: grid; grid-template-columns: 52px auto; margin-bottom: 9px; color: var(--ink-soft); }
  .contact__address { color: var(--ink-soft); }
</style>
</head>
<body>
  <section class="card card--front" aria-label="Visitenkarte Vorderseite">
    <div class="front-brand">
      <span class="front-brand__square"></span>
      <span class="front-brand__name">KLW GmbH</span>
    </div>
  </section>

  <section class="card card--back" aria-label="Visitenkarte Rückseite">
    <svg class="back-shape" width="520" height="326" viewBox="0 0 520 326" aria-hidden="true">
      <defs>
        <linearGradient id="band-top" x1="0" x2="1" y1="0" y2="0">
          <stop offset="0" stop-color="#d83a36"/>
          <stop offset="1" stop-color="#e2703a"/>
        </linearGradient>
        <linearGradient id="band-bottom" x1="0" x2="1" y1="0" y2="0">
          <stop offset="0" stop-color="#e2703a"/>
          <stop offset="1" stop-color="#d83a36"/>
        </linearGradient>
      </defs>
      <rect x="0" y="0" width="520" height="326" fill="url(#band-bottom)"/>
      <rect x="0" y="0" width="520" height="12" fill="url(#band-top)"/>
      <path d="M0 12 H420 Q520 12 520 70 V300 H120 Q40 300 0 278 Z" fill="#ffffff"/>
    </svg>

    <div class="back-brand">
      <span class="back-brand__square"></span>
      <span class="back-brand__name">KLW GmbH</span>
    </div>

    <div class="contact">
      <p class="contact__name">Florian Sailer</p>
      <p class="contact__role">Geschäftsführer</p>
      <p class="contact__heading">Kontakt</p>
      <div class="contact__list">
        <span>Tel</span><span>+49 0000 000 39</span>
        <span>Fax</span><span>+49 0000 000 00</span>
        <span>Mobil</span><span>+49 0000 000 39</span>
        <span>E-mail</span><span>fs@klwfenster.de</span>
      </div>
      <p class="contact__heading">Anschrift</p>
      <p class="contact__address">KLW GmbH Am Lindenhang 16-18<br>39274 Wiesental</p>
    </div>
  </section>
</body>
</html>
```